Polished Comb salon has created a lotion and needs help titling.Tides by polished comb ?Polis

The product is for a lotion bottle , my prototype lotion bottle size is an 8oz black lotion bottle with pump. I want the label in florescent green. It should tap into the emotion of potential buyers. The design should say choose me 😀(not literally ). Though the text should be clear and punchy . I.e " the skin multi-vitamin." I'm looking for a designer intrigued by the thought of my lotion. The label should be georgeous,informative, with visuals that immediately convey what my product is and how it works.Not distracting, but clear and punchy, with no expectation of someone to read more than a couple of words.The text should support the visual in a way the visual could not. It seems that nowadays visuals are taking over with very little text. The font,color , or punch of color should be enticing.
So here are some particular ideas of points about the lotion that could possibly be put on back as is done by lotion makers.
.ingredients
.TSA approved
.portion of proceeds go to lunch for little ones
.TC circled ( which is for pending trademark)
. I would like the word New in fluorescent on the bottle
.P.O Box address of place of manufacturing product.
. To help skin stay slightly moist,soft,and flexible with a smooth fine grained texture.

Target Market(s)

its a lotion so I want it available for all

Industry/Entity Type

Barber

Colors
9bcb3c

Requirements
Must have
• the word" Tides" and By polished comb...the word new on the bottle visible

```html
<!DOCTYPE html>
<html lang="en">
<head>
<meta charset="utf-8">
<title>Tides by Polished Comb – Lotion Label</title>
<link rel="stylesheet" href="https://fonts.googleapis.com/css2?family=Questrial&family=Montserrat:wght@600;700;800&display=swap">
<style>
  :root {
    --backdrop: #efefef;
    --lime: #8fbf33;
    --lime-bright: #9bcb3c;
    --ink: #111111;
    --label-black: #0d0d0d;
    --white: #ffffff;
  }
  html, body {
    margin: 0;
    padding: 0;
    width: 1000px;
    height: 1200px;
    overflow: hidden;
    background: var(--backdrop);
  }
  .canvas {
    position: relative;
    width: 1000px;
    height: 1200px;
    background: var(--backdrop);
  }
  .label {
    position: absolute;
    left: 290px;
    top: 400px;
    width: 420px;
    height: 640px;
    background: var(--label-black);
    border-radius: 14px;
    overflow: hidden;
  }
  .label-front {
    position: absolute;
    left: 0;
    top: 0;
    width: 420px;
    height: 395px;
    background: var(--lime);
    border-radius: 14px 14px 56px 56px;
    text-align: center;
    color: var(--ink);
  }
  .brand-lockup {
    position: absolute;
    left: 0;
    right: 0;
    top: 122px;
    text-align: center;
  }
  .brand-lockup-inner {
    display: inline-block;
    text-align: left;
  }
  .brand-name {
    margin: 0;
    font-family: "Questrial", sans-serif;
    font-weight: 400;
    font-size: 108px;
    line-height: 1;
    letter-spacing: -3px;
    color: var(--ink);
  }
  .brand-byline {
    margin: 6px 0 0 4px;
    font-family: "Montserrat", sans-serif;
    font-weight: 800;
    font-size: 15px;
    line-height: 1;
    letter-spacing: 0.2px;
    color: var(--ink);
  }
  .tagline {
    position: absolute;
    left: 0;
    right: 0;
    top: 283px;
    margin: 0;
    font-family: "Montserrat", sans-serif;
    font-weight: 800;
    font-size: 19px;
    color: var(--ink);
  }
  .description {
    position: absolute;
    left: 78px;
    right: 62px;
    top: 316px;
    margin: 0;
    font-family: "Montserrat", sans-serif;
    font-weight: 700;
    font-size: 11.5px;
    line-height: 1.42;
    text-align: justify;
    text-align-last: center;
    color: var(--ink);
  }
  .new-flag {
    position: absolute;
    left: 0;
    right: 0;
    top: 422px;
    margin: 0;
    font-family: "Montserrat", sans-serif;
    font-weight: 800;
    font-size: 22px;
    letter-spacing: 5px;
    text-align: center;
    color: var(--lime-bright);
  }
  .benefit {
    position: absolute;
    left: 0;
    right: 0;
    top: 475px;
    margin: 0;
    font-family: "Montserrat", sans-serif;
    font-weight: 700;
    font-size: 19.5px;
    line-height: 1.6;
    text-align: center;
    color: var(--white);
  }
  .net-weight {
    position: absolute;
    left: 0;
    right: 0;
    top: 594px;
    margin: 0;
    font-family: "Montserrat", sans-serif;
    font-weight: 600;
    font-size: 17px;
    text-align: center;
    color: var(--white);
  }
</style>
</head>
<body>
  <main class="canvas">
    <section class="label">
      <div class="label-front">
        <div class="brand-lockup">
          <div class="brand-lockup-inner">
            <h1 class="brand-name">Tides</h1>
            <p class="brand-byline">BY POLISHED COMB</p>
          </div>
        </div>
        <h2 class="tagline">THE SKIN MULTI-VITAMIN</h2>
        <p class="description">Lorem ipsum dolor sit amet, consectetur adipisicing elit, sed do eiusmod tempor incididunt ut labore et dolore magna aliqua.</p>
      </div>
      <p class="new-flag">NEW</p>
      <p class="benefit">KEEPS SKIN SOFT,<br>SMOOTH AND SLIGHTLY MOIST</p>
      <p class="net-weight">Net Weight: 8oz</p>
    </section>
  </main>
</body>
</html>
```